Innovative cost reduction consultant needs to build a group of technical advisors

We need to share our message and compassion for developing cost reduction in the automotive industry. We create opportunities for immediate innovation, by developing cost reduction solutions across suppliers with related process. Attached is an existing Power Point, but it needs improvement. Most of all, a good compelling story, why experts should join us.

Target Market(s)

Automotive industry, supply chain management

Industry/Entity Type

Automotive

Font styles to use
Serif
Sans Serif

Requirements
Must have
• Better visual graphics. There are a few, but they are not as visually appearing as I would like. A graphic with data should have a better visual impact then the ones that I created. I would like to share the message, that I am providing a solution for the automotive industry. The goal is to reduce costs and improve supplier and OEM relationships. The objective is to do so by creating opportunities for immediate innovation, by developing cost reduction solutions across suppliers with related processes. This message may need a visual graphic, which is missing from the presentation.
Nice to have
• Challenge my story and presentation. Does this make sense to you, and what is your opinions of the subject. Or, a relevant news source to validate the story.
Should not have
• I have not decided on the name of the venture or logo. So, let's just use my name as the source or writer. Marcus Delby, Cost Reduction Specialist. Thanks,

```html
<!DOCTYPE html>
<html lang="en">
<head>
<meta charset="utf-8">
<title>Supplier Innovation Model</title>
<link rel="stylesheet" href="https://fonts.googleapis.com/css2?family=Roboto+Condensed:wght@400;700&display=swap">
<style>
  :root {
    --navy-deep: #0b3575;
    --navy-light: #2563b3;
    --title-ink: #e9ecef;
    --stripe-line: #d6d6d6;
    --stripe-base: #f7f7f7;
    --stripe-shade: #9c9c9c;
    --footer-blue: #1b9be0;
    --teal: #3aaab6;
    --teal-dark: #23717b;
    --orange: #f37a33;
    --orange-dark: #b8501a;
    --crimson: #b3183d;
    --crimson-dark: #7a0d27;
    --green-light: #3fae48;
    --green-dark: #1b7a2a;
    --purple: #7b2b8f;
    --ink-navy: #123f8a;
    --bullet: #27a8e0;
    --ring-blue: #1c4f9c;
    --dash: #8a8a8a;
  }
  * { box-sizing: border-box; margin: 0; padding: 0; }
  html, body { width: 1200px; height: 650px; overflow: hidden; background: #ffffff; }
  .canvas {
    position: relative;
    width: 1200px;
    height: 650px;
    overflow: hidden;
    font-family: "Roboto Condensed", "Arial Narrow", sans-serif;
  }
  .header-band {
    position: absolute; left: 0; top: 0; width: 1200px; height: 189px;
    background: linear-gradient(180deg, var(--navy-deep) 0%, #14468f 55%, var(--navy-light) 100%);
    display: flex; flex-direction: column; align-items: center; justify-content: center;
    padding-top: 6px;
  }
  .headline {
    color: var(--title-ink);
    font-weight: 700;
    text-align: center;
    line-height: 1.2;
    text-shadow: 0 2px 3px rgba(0,0,0,0.45);
  }
  .headline .line-one { display: block; font-size: 39px; }
  .headline .line-two { display: block; font-size: 34px; }
  .striped-field {
    position: absolute; left: 0; top: 189px; width: 1200px; height: 435px;
    background:
      repeating-linear-gradient(180deg, var(--stripe-line) 0 6px, transparent 6px 15px),
      linear-gradient(90deg, var(--stripe-base) 0%, #eeeeee 45%, #c9c9c9 75%, var(--stripe-shade) 100%);
  }
  .footer-band {
    position: absolute; left: 0; top: 624px; width: 1200px; height: 26px;
    background: var(--footer-blue);
  }
  .diagram { position: absolute; left: 0; top: 0; width: 1200px; height: 650px; }
  .diagram text { font-family: "Roboto Condensed", "Arial Narrow", sans-serif; }
  .source-label { fill: #ffffff; font-weight: 700; font-size: 11.5px; }
  .arrow-label { fill: #ffffff; font-weight: 700; font-size: 17.5px; }
  .box-heading { fill: var(--ink-navy); font-weight: 700; font-size: 17px; }
  .box-item { fill: #2b2b2b; font-size: 16px; }
  .bullet { fill: var(--bullet); }
  .group-label { fill: var(--ink-navy); font-weight: 700; font-size: 31px; }
</style>
</head>
<body>
<main class="canvas">
  <header class="header-band">
    <h1 class="headline">
      <span class="line-one">Going beyond even the most advanced supplier collaboration</span>
      <span class="line-two">and innovative models and inviting strategic innovation opportunities</span>
    </h1>
  </header>

  <div class="striped-field"></div>
  <div class="footer-band"></div>

  <svg class="diagram" viewBox="0 0 942 510" preserveAspectRatio="none" aria-label="Innovation flow from sources to the supplier group">
    <defs>
      <linearGradient id="greenFlow" x1="0" y1="0" x2="0" y2="1">
        <stop offset="0" stop-color="var(--green-light)"/>
        <stop offset="1" stop-color="var(--green-dark)"/>
      </linearGradient>
      <radialGradient id="pinFace" cx="0.45" cy="0.4" r="0.7">
        <stop offset="0" stop-color="#ffffff"/>
        <stop offset="0.7" stop-color="#eef0f3"/>
        <stop offset="1" stop-color="#c7ccd4"/>
      </radialGradient>
      <linearGradient id="ringBlue" x1="0" y1="0" x2="0" y2="1">
        <stop offset="0" stop-color="#3a72c4"/>
        <stop offset="1" stop-color="#123d80"/>
      </linearGradient>
    </defs>

    <!-- source arrows -->
    <g class="source-arrow rnd">
      <polygon points="55,236 78,226 100,248 78,272 55,262" fill="var(--teal-dark)"/>
      <polygon points="80,252 208,252 208,243 236,268 208,293 208,284 80,284 95,268" fill="var(--teal)"/>
      <text class="source-label" x="106" y="273">R&amp;D Industry</text>
    </g>
    <g class="source-arrow universities">
      <polygon points="55,282 78,272 100,294 78,318 55,308" fill="var(--orange-dark)"/>
      <polygon points="80,298 208,298 208,289 236,314 208,339 208,330 80,330 95,314" fill="var(--orange)"/>
      <text class="source-label" x="106" y="319">Universities</text>
    </g>
    <g class="source-arrow advisors">
      <polygon points="55,328 78,318 100,340 78,364 55,354" fill="var(--crimson-dark)"/>
      <polygon points="80,344 208,344 208,335 236,360 208,385 208,376 80,376 95,360" fill="var(--crimson)"/>
      <text class="source-label" x="106" y="365">Technical Advisors</text>
    </g>

    <!-- forecast box -->
    <g class="forecast-box">
      <rect x="330" y="164" width="220" height="128" rx="8" fill="#ffffff" stroke="var(--dash)" stroke-dasharray="2 2"/>
      <text class="box-heading" x="440" y="194" text-anchor="middle">Forecast data</text>
      <text class="box-item" x="440" y="220" text-anchor="middle"><tspan class="bullet">•</tspan> Identified opportunities</text>
      <text class="box-item" x="440" y="244" text-anchor="middle"><tspan class="bullet">•</tspan> ROI Presentation</text>
      <text class="box-item" x="440" y="268" text-anchor="middle"><tspan class="bullet">•</tspan> Project Planning</text>
    </g>

    <!-- solution categories box -->
    <g class="solutions-box">
      <path d="M338,333 H542 a8,8 0 0 1 8,8 V395 H642 a8,8 0 0 1 8,8 V458 a8,8 0 0 1 -8,8 H240 a8,8 0 0 1 -8,-8 V403 a8,8 0 0 1 8,-8 H330 V341 a8,8 0 0 1 8,-8 Z"
            fill="#ffffff" stroke="var(--dash)" stroke-dasharray="2 2"/>
      <text class="box-heading" x="440" y="357" text-anchor="middle">Solution Categories:</text>
      <text class="box-item" x="440" y="381" text-anchor="middle"><tspan class="bullet">•</tspan> Raw Materials</text>
      <text class="box-item" x="440" y="405" text-anchor="middle"><tspan class="bullet">•</tspan> Material processing</text>
      <text class="box-item" x="440" y="430" text-anchor="middle"><tspan class="bullet">•</tspan> Machining <tspan class="bullet">•</tspan> Assembly <tspan class="bullet">•</tspan> Packaging / Transportation</text>
      <text class="box-item" x="440" y="453" text-anchor="middle"><tspan class="bullet">•</tspan> Tooling &amp; Capital <tspan class="bullet">•</tspan> Inspection &amp; Testing</text>
    </g>

    <!-- supplier survey band -->
    <g class="survey-band">
      <rect x="330" y="293" width="210" height="40" fill="var(--purple)"/>
      <text class="arrow-label" x="435" y="319" text-anchor="middle">Supplier Survey</text>
    </g>

    <!-- innovative technology arrow -->
    <g class="flow-arrow innovation">
      <polygon points="212,272 298,272 298,246 347,313 298,380 298,354 212,354" fill="url(#greenFlow)"/>
      <text class="arrow-label" x="280" y="306" text-anchor="middle">Innovative</text>
      <text class="arrow-label" x="280" y="331" text-anchor="middle">Technology</text>
    </g>

    <!-- opportunities double arrow -->
    <g class="flow-arrow opportunities">
      <polygon points="505,313 552,246 552,272 672,272 672,246 720,313 672,380 672,354 552,354 552,380" fill="url(#greenFlow)"/>
      <text class="arrow-label" x="612" y="306" text-anchor="middle">Opportunities</text>
      <text class="arrow-label" x="612" y="331" text-anchor="middle">Solutions</text>
    </g>

    <!-- supplier group pin -->
    <g class="supplier-pin">
      <path d="M775,232 a72,72 0 0 1 28,138 L775,428 L747,370 a72,72 0 0 1 28,-138 Z" fill="url(#ringBlue)"/>
      <circle cx="775" cy="304" r="62" fill="url(#pinFace)"/>
      <text class="group-label" x="775" y="299" text-anchor="middle">Supplier</text>
      <text class="group-label" x="775" y="336" text-anchor="middle">Group</text>
    </g>
  </svg>
</main>
</body>
</html>
```